Local fast-growing company in the service sector

We are looking for a modern business card design, which should also appear on our letterheads

Target Market(s)

Private and industrial sectors

Contact Information for Business Card

Vorname Name
Kellberger Str. 18
72418 Kellstadt
Tel.: 07146-839214-0
Name@agentur-kvtl.de

Colors
9d9d9d
919191
aaaaaa

Requirements
Must have
• The logo (file) in silver

```html
<!DOCTYPE html>
<html lang="de">
<head>
<meta charset="utf-8">
<title>KVTL Visitenkarte</title>
<link rel="stylesheet" href="https://fonts.googleapis.com/css2?family=Open+Sans:wght@400;600;700&display=swap">
<style>
  :root {
    --stage: #2b2c2f;
    --card-dark-top: #5b5a59;
    --card-dark-bottom: #2c2c2c;
    --card-light: #ffffff;
    --silver: #9d9d9d;
    --silver-light: #aaaaaa;
    --silver-mid: #919191;
    --ink: #1e1e1e;
    --icon: #6f6f6f;
  }
  * { box-sizing: border-box; margin: 0; padding: 0; }
  html, body {
    width: 1200px; height: 864px; overflow: hidden;
    background: var(--stage);
    font-family: "Open Sans", Arial, sans-serif;
  }
  .stage { position: relative; width: 1200px; height: 864px; }
  .card {
    position: absolute; width: 520px; height: 336px; top: 264px;
    border-radius: 4px; overflow: hidden;
  }
  .card--front {
    left: 50px;
    background: linear-gradient(180deg, var(--card-dark-top), var(--card-dark-bottom));
  }
  .card--back { left: 630px; background: var(--card-light); }
  .brand { position: absolute; display: flex; align-items: center; gap: 14px; }
  .brand__mark {
    width: 46px; height: 46px; border-radius: 50%;
    background: var(--silver-mid);
  }
  .brand__text { display: flex; flex-direction: column; line-height: 1; }
  .brand__name {
    font-weight: 700; font-size: 58px; letter-spacing: 2px;
    color: var(--silver);
  }
  .brand__url {
    font-weight: 400; font-size: 19px; letter-spacing: 1px;
    color: var(--silver); margin-top: 4px;
  }
  .card--front .brand { left: 130px; top: 118px; }
  .card--front .brand__name,
  .card--front .brand__url { color: var(--silver-light); }
  .card--back .brand { left: 200px; top: 62px; }
  .holder {
    position: absolute; left: 52px; top: 158px;
    font-weight: 700; font-size: 19px; color: var(--ink);
  }
  .contact {
    position: absolute; right: 30px; bottom: 36px;
    list-style: none; text-align: right;
    font-size: 15px; line-height: 22px; color: var(--ink);
  }
  .contact li { display: flex; align-items: center; justify-content: flex-end; gap: 8px; }
  .contact svg { width: 12px; height: 12px; fill: var(--icon); }
</style>
</head>
<body>
<main class="stage">
  <section class="card card--front" aria-label="Vorderseite">
    <div class="brand">
      <span class="brand__mark"></span>
      <div class="brand__text">
        <span class="brand__name">KVTL</span>
        <span class="brand__url">agentur-kvtl.de</span>
      </div>
    </div>
  </section>

  <section class="card card--back" aria-label="Rückseite">
    <div class="brand">
      <span class="brand__mark"></span>
      <div class="brand__text">
        <span class="brand__name">KVTL</span>
        <span class="brand__url">agentur-kvtl.de</span>
      </div>
    </div>
    <p class="holder">Vorname Name</p>
    <ul class="contact">
      <li>07146-839214-0
        <svg viewBox="0 0 24 24" aria-hidden="true"><path d="M6.6 10.8a15 15 0 0 0 6.6 6.6l2.2-2.2c.3-.3.7-.4 1-.2 1.1.4 2.3.6 3.6.6.6 0 1 .4 1 1V20c0 .6-.4 1-1 1A17 17 0 0 1 3 4c0-.6.4-1 1-1h3.5c.6 0 1 .4 1 1 0 1.3.2 2.5.6 3.6.1.3 0 .7-.2 1z"/></svg>
      </li>
      <li>Name@agentur-kvtl.de
        <svg viewBox="0 0 24 24" aria-hidden="true"><path d="M2 5h20v14H2z M4 7v.5l8 5 8-5V7l-8 5z" fill-rule="evenodd"/></svg>
      </li>
      <li>www.agentur-kvtl.de
        <svg viewBox="0 0 24 24" aria-hidden="true"><circle cx="12" cy="12" r="10"/></svg>
      </li>
      <li class="contact__address">Kellberger Str. 18 72418 Kellstadt</li>
    </ul>
  </section>
</main>
</body>
</html>
```